Upmarket Dessert Lounge needs a Business Card Design

We are an upmarket dessert lounge needing a business card to match our image.

We want something that is simple yet beautiful, feminine, classy, sophisticated and elegant. We want it to stand out and don't mind if it is bold.

The design should include our logo and colours of red or maroon with gold highlights. We don't mind if black is used.

Marlow & Quince

Target Market(s)

For those who like to indulge or treat themselves and give in to their temptations on good quality desserts.

Industry/Entity Type

Business

Requirements
Must have
• Must include our logo and our name

Marlow & Quince

M & Q

```html
<!DOCTYPE html>
<html lang="en">
<head>
<meta charset="utf-8">
<title>Marlow &amp; Quince — Business Card</title>
<link rel="stylesheet" href="https://fonts.googleapis.com/css2?family=Lora:wght@400&family=Open+Sans:wght@400&display=swap">
<style>
  :root {
    --backdrop: #f2e4e4;
    --maroon: #6a1e1d;
    --maroon-deep: #5a1716;
    --gold: #e2b07c;
    --gold-soft: #c9925d;
    --ivory: #f6ece6;
  }
  * { box-sizing: border-box; margin: 0; padding: 0; }
  html, body {
    width: 1200px;
    height: 951px;
    overflow: hidden;
    background: var(--backdrop);
  }
  .canvas {
    position: relative;
    width: 1200px;
    height: 951px;
  }
  .card {
    position: absolute;
    width: 580px;
    height: 330px;
    background: var(--maroon);
    border-radius: 22px;
    overflow: hidden;
  }
  .card--front { left: 80px; top: 90px; }
  .card--back { left: 540px; top: 520px; }

  .corner-ornament {
    position: absolute;
    top: 0;
    right: 0;
    width: 250px;
    height: 110px;
    background: radial-gradient(ellipse at 65% 30%, rgba(226,176,124,0.55), rgba(226,176,124,0.15) 60%, rgba(226,176,124,0) 80%);
  }
  .brand-name {
    position: absolute;
    left: 0;
    top: 118px;
    width: 410px;
    text-align: center;
    font-family: "Lora", serif;
    font-weight: 400;
    font-size: 34px;
    letter-spacing: 1px;
    color: var(--gold);
    text-transform: uppercase;
  }
  .website {
    position: absolute;
    left: 0;
    top: 248px;
    width: 410px;
    text-align: center;
    font-family: "Lora", serif;
    font-size: 17px;
    letter-spacing: 1.5px;
    color: var(--gold);
  }

  .monogram {
    position: absolute;
    left: 30px;
    top: 118px;
    width: 200px;
    text-align: center;
    font-family: "Lora", serif;
    font-weight: 400;
    font-size: 62px;
    color: var(--gold);
  }
  .contact {
    position: absolute;
    right: 62px;
    top: 92px;
    text-align: left;
    font-family: "Open Sans", sans-serif;
    color: var(--ivory);
  }
  .contact__name {
    font-size: 21px;
    color: var(--gold);
    margin-bottom: 16px;
  }
  .contact__address {
    font-size: 15px;
    line-height: 1.3;
    margin-bottom: 18px;
  }
  .contact__lines {
    font-size: 15px;
    line-height: 1.4;
    text-align: right;
  }
  .contact__email-domain { color: var(--gold); }
  .edge-band {
    position: absolute;
    right: 22px;
    top: 170px;
    width: 10px;
    height: 72px;
    background: linear-gradient(90deg, var(--gold-soft), var(--gold));
  }
</style>
</head>
<body>
<main class="canvas">
  <section class="card card--front" aria-label="Business card front">
    <div class="corner-ornament" role="img" aria-label="Gold floral flourish ornament in the corner"></div>
    <p class="brand-name">Marlow &amp; Quince</p>
    <p class="website">www.marlow&amp;quince.com</p>
  </section>

  <section class="card card--back" aria-label="Business card back">
    <p class="monogram">M&amp;Q</p>
    <div class="contact">
      <p class="contact__name">Marlow &amp; Quince</p>
      <p class="contact__address">48 Bellmore Street, Suite 210<br>Ashford, Vermont 05214</p>
      <p class="contact__lines">802-555-0148<br>info@<span class="contact__email-domain">marlow&amp;quince</span>.com</p>
    </div>
    <div class="edge-band"></div>
  </section>
</main>
</body>
</html>
```